LED-Leuchtboxen
Zielgruppe
Wir sind ein Ingenieurbüro und bieten Beratungsdienstleistungen an. Thema ist z.B. Sicherheit in öffentlichen Verwaltungen, Sicherheit von Mitarbeitern am Arbeitsplatz.
B+W Ingenieurgesellschaft für Notfall- und Gefahrenmanagement mbH
Lindenweg 17
70439 Stuttgart
Telefon 0711 8853 294
E-Mail info @bw-vorsorge.com
Web www.bw-vorsorge.com
Wir sind auf einer Messe und brauchen dafür zwei auffällige Designs für zwei LED-Leuchtboxen (Lumbra Flex). Die Besucher der Messe sind Mitarbeiter von öffentlichen Verwaltungen.
Aufgabenstellung
Für die beiden LED-Leuchtboxen brauchen wir farbige und auffällige Bilder/Designs, die aber nicht überfüllt sind und die man sich gerne anschaut. z.B. ein gutes Foto was entfernt etwas mit Sicherheit zu tun hat.
1. Box: Auffälliges Bild als Image-Werbung mit Icon, Firmennamen und vielleicht einem knackigen Spruch ('Heute war ich schon Bitch, Arschloch und wurde bedroht!') Beispiele: Siehe fOTarium-Bilder im Anhang.
2. Box: Was wir tun.... (Sicherheit in öffentlichen Verwaltungen: - Notfall- und Krisenmanagement, - KRITIS-Bewertungen, - Fachplanung Sicherungstechnik, - Amok-Konzepte). Hier muss kein Foto im Hintergrund.
An die Vorgaben von Lumbra für die Druckdaten und die Maße ist sich unbedingt zu halten!!! Siehe beide Dateien im Anhang

```html
<!DOCTYPE html>
<html lang="de">
<head>
<meta charset="utf-8">
<title>B+W Leuchtboxen</title>
<link href="https://fonts.googleapis.com/css2?family=Barlow+Condensed:ital,wght@0,500;0,700;1,500;1,700&family=Hind:wght@600&family=Michroma&display=swap" rel="stylesheet">
<style>
  :root{
    --page:#e9e9ea;
    --blue:#1d5fb3;
    --orange:#f26a1b;
    --ink:#2b2b2f;
    --white:#ffffff;
  }
  *{margin:0;padding:0;box-sizing:border-box}
  html,body{width:1200px;height:1117px;overflow:hidden;background:var(--page)}
  .stage{position:relative;width:1200px;height:1117px}
  .box{position:absolute;top:36px;width:420px;height:1045px;overflow:hidden;box-shadow:0 6px 24px rgba(0,0,0,.18)}
  .box--image{left:160px}
  .box--services{left:620px}
  .box-bg{position:absolute;inset:0;width:100%;height:100%}
  .abs{position:absolute}

  .photo-area{left:0;top:70px;width:380px;height:570px;
    background:radial-gradient(ellipse 85% 75% at 20% 70%, rgba(110,80,55,.95) 0%, rgba(80,62,48,.7) 45%, rgba(60,55,60,0) 100%)}

  .lockup{display:flex;align-items:center;gap:14px}
  .lockup--foot{left:66px;top:668px}
  .lockup--top{left:70px;top:94px}
  .brand{display:flex;align-items:center;gap:8px;font-family:"Barlow Condensed",sans-serif;font-weight:700;line-height:1;white-space:nowrap}
  .brand-square{display:block;background:currentColor}
  .brand--hero{left:214px;top:82px;color:var(--blue);font-size:66px}
  .brand--hero .brand-square{width:16px;height:16px}
  .brand--foot{color:var(--white);font-size:40px}
  .brand--foot .brand-square{width:10px;height:10px}
  .brand--top{color:var(--blue);font-size:44px}
  .brand--top .brand-square{width:11px;height:11px}

  .company{font-family:"Michroma",sans-serif;font-size:7.6px;line-height:1.4;text-transform:uppercase;letter-spacing:.2px;white-space:nowrap}
  .company--light{color:var(--white)}
  .company--dark{color:var(--ink)}

  .slogan{font-family:"Barlow Condensed",sans-serif;font-style:italic;font-weight:700;text-transform:uppercase;line-height:.9;white-space:nowrap}
  .slogan-lead{left:172px;top:218px;font-size:18px;font-weight:500;color:var(--ink)}
  .slogan-hit{left:160px;top:234px;font-size:88px;color:var(--blue);letter-spacing:-1px}
  .slogan-word{left:182px;top:318px;font-size:32px;font-weight:500;color:var(--ink)}
  .slogan-row{left:200px;top:346px;display:flex;align-items:baseline;gap:6px}
  .slogan-und{font-size:22px;font-weight:500;color:var(--ink)}
  .slogan-alert{font-size:48px;color:var(--orange)}
  .slogan-alert2{left:198px;top:386px;font-size:48px;color:var(--orange)}

  .headline{left:0;width:420px;top:210px;text-align:center;font-family:"Barlow Condensed",sans-serif;font-style:italic;font-weight:700;font-size:54px;line-height:.98;color:var(--white);text-transform:uppercase}

  .services{left:69px;top:440px;width:290px;list-style:none}
  .service{display:flex;align-items:flex-start;gap:20px;padding:6px 0;border-bottom:1px solid rgba(120,170,235,.7);font-family:"Barlow Condensed",sans-serif;font-style:italic;font-weight:700;font-size:28px;line-height:.9;color:var(--white);text-transform:uppercase}
  .service:last-child{border-bottom:none}
  .service-mark{flex:0 0 22px;width:22px;height:22px;border:2px solid var(--white);margin:4px 0 0 6px}
  .service:nth-child(1){height:72px;padding-top:6px}
  .service:nth-child(2){height:58px;padding-top:15px}
  .service:nth-child(3){height:88px;padding-top:14px}
  .service:nth-child(4){padding-top:14px}

  .contact{list-style:none;font-family:"Hind",sans-serif;font-weight:600;font-size:20px;line-height:26px;color:var(--white)}
  .contact--left{left:118px;top:800px}
  .contact--right{left:127px;top:797px}
  .contact li{display:flex;align-items:center;gap:12px}
  .contact li.cont{padding-left:30px}
  .contact svg{flex:0 0 18px;width:18px;height:18px}
</style>
</head>
<body>
<main class="stage">

  <section class="box box--image">
    <svg class="box-bg" viewBox="0 0 595 1480" preserveAspectRatio="none" aria-hidden="true">
      <defs>
        <linearGradient id="imgSky" x1="0" y1="0" x2="0" y2="1">
          <stop offset="0" stop-color="#8091c2"/>
          <stop offset=".3" stop-color="#d5dcef"/>
          <stop offset=".55" stop-color="#9aa3bf"/>
          <stop offset=".66" stop-color="#2f3036"/>
          <stop offset="1" stop-color="#262628"/>
        </linearGradient>
        <linearGradient id="orangeFill" x1="0" y1="0" x2="1" y2="1">
          <stop offset="0" stop-color="#f7892f"/>
          <stop offset="1" stop-color="#ee5f12"/>
        </linearGradient>
      </defs>
      <rect width="595" height="1480" fill="url(#imgSky)"/>
      <path d="M0,1100 L140,1110 L0,1480 Z" fill="#1e1e20"/>
      <path d="M0,1440 L105,1082 L595,1018 L595,1036 L128,1100 L0,1480 Z" fill="#2f79d6"/>
      <path d="M140,1112 L595,1040 L595,1480 L0,1480 L0,1476 Z" fill="url(#orangeFill)"/>
      <path d="M240,1480 L282,1408 L595,1330 L595,1480 Z" fill="#ffffff"/>
    </svg>
    <div class="abs photo-area" role="img" aria-label="Foto: gestresste Mitarbeiterin am Telefon im Büro"></div>

    <div class="abs brand brand--hero"><span class="brand-square"></span>B+W</div>

    <p class="abs slogan slogan-lead">Heute war ich schon</p>
    <p class="abs slogan slogan-hit">Bitch,</p>
    <p class="abs slogan slogan-word">Arschloch</p>
    <p class="abs slogan slogan-row"><span class="slogan-und">und</span><span class="slogan-alert">wurde</span></p>
    <p class="abs slogan slogan-alert2">bedroht!</p>

    <div class="abs lockup lockup--foot">
      <div class="brand brand--foot"><span class="brand-square"></span>B+W</div>
      <p class="company company--light">B+W Ingenieurgesellschaft<br>für Notfall- und<br>Gefahrenmanagement mbH</p>
    </div>

    <ul class="abs contact contact--left">
      <li><svg viewBox="0 0 24 24"><path d="M12 2a7 7 0 0 0-7 7c0 5 7 13 7 13s7-8 7-13a7 7 0 0 0-7-7zm0 9.5A2.5 2.5 0 1 1 12 6.5a2.5 2.5 0 0 1 0 5z" fill="#fff"/></svg>Lindenweg 17</li>
      <li class="cont">70439 Stuttgart</li>
      <li><svg viewBox="0 0 24 24"><circle cx="12" cy="12" r="10" fill="none" stroke="#fff" stroke-width="1.6"/><path d="M8.5 7.5l2 2-1 1.5c.7 1.4 1.6 2.3 3 3l1.5-1 2 2-1.2 1.6c-3.6-.3-6.6-3.3-6.9-6.9z" fill="#fff"/></svg>0711 8853 294</li>
      <li><svg viewBox="0 0 24 24"><rect x="3" y="6" width="18" height="12" fill="none" stroke="#fff" stroke-width="1.6"/><path d="M3 6l9 7 9-7" fill="none" stroke="#fff" stroke-width="1.6"/></svg>info @bw-vorsorge.com</li>
      <li><svg viewBox="0 0 24 24"><circle cx="12" cy="12" r="9" fill="none" stroke="#fff" stroke-width="1.6"/><ellipse cx="12" cy="12" rx="4" ry="9" fill="none" stroke="#fff" stroke-width="1.4"/><path d="M3 12h18M5 7.5h14M5 16.5h14" stroke="#fff" stroke-width="1.2"/></svg>www.bw-vorsorge.com</li>
    </ul>
  </section>

  <section class="box box--services">
    <svg class="box-bg" viewBox="0 0 595 1480" preserveAspectRatio="none" aria-hidden="true">
      <defs>
        <linearGradient id="svcSky" x1="0" y1="0" x2="1" y2="1">
          <stop offset="0" stop-color="#7d8ec0"/>
          <stop offset="1" stop-color="#c4cde8"/>
        </linearGradient>
        <linearGradient id="svcBlue" x1="0" y1="0" x2="0" y2="1">
          <stop offset="0" stop-color="#2f5b9e"/>
          <stop offset="1" stop-color="#22407a"/>
        </linearGradient>
        <linearGradient id="svcOrange" x1="0" y1="0" x2="1" y2="1">
          <stop offset="0" stop-color="#ee5f12"/>
          <stop offset="1" stop-color="#f7892f"/>
        </linearGradient>
        <linearGradient id="svcOrange2" x1="0" y1="0" x2="1" y2="1">
          <stop offset="0" stop-color="#f7892f"/>
          <stop offset="1" stop-color="#ee5f12"/>
        </linearGradient>
      </defs>
      <rect width="595" height="1480" fill="url(#svcSky)"/>
      <rect y="400" width="595" height="1080" fill="url(#svcBlue)"/>
      <path d="M0,195 L595,330 L595,610 L0,485 Z" fill="url(#svcOrange)"/>
      <path d="M0,1440 L105,1082 L595,1018 L595,1036 L128,1100 L0,1480 Z" fill="#2f79d6"/>
      <path d="M140,1112 L595,1040 L595,1480 L0,1480 L0,1476 Z" fill="url(#svcOrange2)"/>
      <path d="M240,1480 L282,1408 L595,1330 L595,1480 Z" fill="#ffffff"/>
    </svg>

    <div class="abs lockup lockup--top">
      <div class="brand brand--top"><span class="brand-square"></span>B+W</div>
      <p class="company company--dark">B+W Ingenieurgesellschaft<br>für Notfall- und<br>Gefahrenmanagement mbH</p>
    </div>

    <h1 class="abs headline">Sicherheit<br>in öffentlichen<br>Verwaltungen:</h1>

    <ul class="abs services">
      <li class="service"><span class="service-mark"></span><span>Notfall- und<br>Krisenmanagement,</span></li>
      <li class="service"><span class="service-mark"></span><span>KRITIS-Bewertungen,</span></li>
      <li class="service"><span class="service-mark"></span><span>Fachplanung<br>Sicherungstechnik,</span></li>
      <li class="service"><span class="service-mark"></span><span>Amok-Konzepte</span></li>
    </ul>

    <ul class="abs contact contact--right">
      <li><svg viewBox="0 0 24 24"><path d="M12 2a7 7 0 0 0-7 7c0 5 7 13 7 13s7-8 7-13a7 7 0 0 0-7-7zm0 9.5A2.5 2.5 0 1 1 12 6.5a2.5 2.5 0 0 1 0 5z" fill="#fff"/></svg>Lindenweg 17</li>
      <li class="cont">70439 Stuttgart</li>
      <li><svg viewBox="0 0 24 24"><circle cx="12" cy="12" r="10" fill="none" stroke="#fff" stroke-width="1.6"/><path d="M8.5 7.5l2 2-1 1.5c.7 1.4 1.6 2.3 3 3l1.5-1 2 2-1.2 1.6c-3.6-.3-6.6-3.3-6.9-6.9z" fill="#fff"/></svg>0711 8853 294</li>
      <li><svg viewBox="0 0 24 24"><rect x="3" y="6" width="18" height="12" fill="none" stroke="#fff" stroke-width="1.6"/><path d="M3 6l9 7 9-7" fill="none" stroke="#fff" stroke-width="1.6"/></svg>info @bw-vorsorge.com</li>
      <li><svg viewBox="0 0 24 24"><circle cx="12" cy="12" r="9" fill="none" stroke="#fff" stroke-width="1.6"/><ellipse cx="12" cy="12" rx="4" ry="9" fill="none" stroke="#fff" stroke-width="1.4"/><path d="M3 12h18M5 7.5h14M5 16.5h14" stroke="#fff" stroke-width="1.2"/></svg>www.bw-vorsorge.com</li>
    </ul>
  </section>

</main>
</body>
</html>
```